WEBSITE DESIGN, VELTRA paint and panel

We are in need of a website for Veltra Paint & Panel based in Brisbane, Australia. We are a boutique Automotive Paint & Panel Company that provides services to all makes and models of vehicles. We have attached a logo that is still in draft stage but gives you an idea of the colour scheme and fonts and overall impact we are looking for. We are after a white background so this is clean and crisp whilst being sleek, modern and professional. The website must represent our slogan of Glowing finish on the Gleaming frame. The website must therefore be visually effective as our product is to get colour and placement on vehicle body's correct so the website must have this impact on our clients. We are after a widescreen webpage that is simple and logical to navigate. The final design should give clients the confidence that we can deliver on our promise.
Updates

Target Market(s)

Vehicle Owners who have a need for panel repairs and people who want to reinvigorate their car with a new coat of paint.

Industry/Entity Type

Car Repair

Coding

Coded - Design and coding required

Number of Pages Required

5+ page

Font styles to use
Sans Serif

Colors
ffffff
ffc214
000000

Requirements
Must have
• Page 1 - Home Page
• Page 2 - Our Process
• Page 3 - Private Customers
• Page 4 - Fleet & Corporate
• Page 5 - Insurance
• Page 6 - Get a Quote
• Page 7 - Connect (Contacts Page)
• Same font and colour scheme as the logo.
Should not have
• A typical mechanical/paint and panel layout which looks like a template website.

```html
<!DOCTYPE html>
<html lang="en">
<head>
<meta charset="utf-8">
<title>Veltra Paint &amp; Panel</title>
<link href="https://fonts.googleapis.com/css2?family=Open+Sans:ital,wght@0,400;0,600;0,700;0,800;1,700;1,800&display=swap" rel="stylesheet">
<style>
:root{
  --black:#0b0b0b;
  --footer:#111213;
  --white:#ffffff;
  --blue:#1f9be3;
  --blue-dark:#0c6fb8;
  --ink:#222222;
  --muted:#7a7a7a;
  --rule:#e3e3e3;
}
*{margin:0;padding:0;box-sizing:border-box}
html,body{width:711px;height:1200px;overflow:hidden}
body{font-family:"Open Sans",Arial,sans-serif;background:var(--white);color:var(--ink);position:relative}

.site-header{position:absolute;top:0;left:0;width:711px;height:28px;background:var(--black);display:flex;align-items:center;justify-content:space-between;padding:0 38px 0 52px;z-index:2}
.brand{color:var(--white);font-weight:700;font-size:11px;letter-spacing:2px;display:flex;align-items:center;gap:5px}
.brand-dot{width:7px;height:7px;background:var(--blue);border-radius:50%}
.main-nav{display:flex;gap:13px}
.main-nav a{color:var(--white);font-size:6.5px;text-decoration:none;font-weight:600}
.main-nav a.active{color:var(--blue)}

.hero{position:absolute;top:28px;left:0;width:711px;height:292px;background:linear-gradient(115deg,#0d3f7a 0%,#1c7fd0 30%,#9fc9e8 55%,#2a6fb8 75%,#0b2f5c 100%)}
.hero-title{position:absolute;top:198px;left:60px;color:var(--white);font-size:25px;font-weight:800;font-style:italic;text-shadow:0 2px 4px rgba(0,0,0,.5)}
.hero-text{position:absolute;top:240px;left:120px;width:470px;color:var(--white);font-size:6px;line-height:9px;text-align:center}

.section-title{position:absolute;left:0;width:711px;text-align:center;font-size:17px;font-weight:700;color:var(--ink)}
.section-title span{color:var(--blue)}
.section-sub{position:absolute;left:0;width:711px;text-align:center;font-size:8px;color:var(--muted)}
.welcome-text{position:absolute;top:390px;left:120px;width:470px;text-align:center;font-size:6px;line-height:9px;color:var(--muted)}

.divider{position:absolute;left:0;width:711px;height:6px}
.divider .line{position:absolute;top:2px;height:1px;background:var(--rule);width:300px}
.divider .mark{position:absolute;left:328px;top:0;width:55px;height:5px;display:flex;gap:3px}
.divider .mark i{flex:1;background:var(--ink)}
.divider .mark i.blue{background:var(--blue)}

.service-card{position:absolute;top:533px;width:187px;height:96px}
.service-photo{position:absolute;inset:0;background:linear-gradient(135deg,#3a5d85,#b9c7d6 50%,#2c3f58)}
.service-label{position:absolute;left:0;bottom:0;width:100%;height:14px;background:var(--blue);color:var(--white);font-size:7px;font-weight:600;text-align:center;line-height:14px}
.service-card.featured .service-photo{background:linear-gradient(135deg,#cfd8e0,#8aa4bd 60%,#4f6a86)}
.service-card.featured .service-label{top:14px;bottom:auto;background:rgba(31,155,227,.9)}
.read-more{position:absolute;left:68px;top:64px;width:50px;height:12px;background:var(--blue-dark);color:var(--white);font-size:6px;text-align:center;line-height:12px}

.post{position:absolute;top:718px;width:290px}
.post-photo{width:290px;height:116px;background:linear-gradient(135deg,#4a78a6,#c8d6e2 50%,#3d5d7c)}
.post-meta{margin-top:12px;font-size:5.5px;color:var(--muted)}
.post-title{margin-top:7px;font-size:6.5px;font-weight:700;color:var(--ink)}
.post-text{margin-top:6px;font-size:5.5px;line-height:8.5px;color:var(--muted)}
.post-author{margin-top:8px;display:flex;align-items:center;gap:6px;font-size:5.5px;color:var(--muted)}
.avatar{width:14px;height:14px;border-radius:50%;background:#9fb6cc}

.site-footer{position:absolute;top:1024px;left:0;width:711px;height:176px;background:var(--footer);color:#bdbdbd}
.footer-col{position:absolute;top:16px}
.footer-col h4{font-size:8px;font-weight:600;color:var(--blue);margin-bottom:10px}
.footer-col p,.footer-col li{font-size:5.5px;line-height:8.5px;list-style:none}
.footer-brand{color:var(--white);font-weight:700;font-size:12px;letter-spacing:2px;margin-bottom:10px}
.footer-col .more{color:var(--blue)}
.email-field{margin-top:8px;width:120px;height:14px;background:#2a2b2c;font-size:5.5px;line-height:14px;padding-left:5px;color:#888}
.subscribe{margin-top:6px;width:40px;height:12px;background:var(--blue);color:var(--white);font-size:5.5px;line-height:12px;text-align:center}
.social{display:grid;grid-template-columns:repeat(2,18px);gap:8px 12px}
.social span{width:18px;height:18px;border-radius:50%;background:#d8d8d8;display:block}
.copyright{position:absolute;bottom:8px;left:0;width:711px;text-align:center;font-size:5.5px;color:#8a8a8a;border-top:1px solid #262728;padding-top:6px}
</style>
</head>
<body>

<header class="site-header">
  <div class="brand"><span class="brand-dot"></span>VELTRA</div>
  <nav class="main-nav">
    <a class="active" href="#">Home</a>
    <a href="#">Our Process</a>
    <a href="#">Private Customers</a>
    <a href="#">Fleet &amp; Corporate Insurance</a>
    <a href="#">Get a Quote</a>
    <a href="#">Contact</a>
  </nav>
</header>

<section class="hero" role="img" aria-label="Painter in protective mask spraying a glossy blue car panel">
  <h1 class="hero-title">Glowing finish on the Gleaming frame</h1>
  <p class="hero-text">Fine automotive refinishing with careful colour matching, panel shaping and a finish built to last on every make and model.</p>
</section>

<h2 class="section-title" style="top:362px">Welcome to <span>Veltra Paint &amp; Panel</span></h2>
<p class="welcome-text">Veltra Paint &amp; Panel is a boutique Brisbane workshop restoring vehicles of every make and model. Our team matches colour precisely, repairs panels with care and returns each car with a finish that looks factory fresh and lasts for years on the road.</p>

<div class="divider" style="top:447px"><div class="line" style="left:25px"></div><div class="mark"><i></i><i class="blue"></i><i></i></div><div class="line" style="left:386px"></div></div>

<h2 class="section-title" style="top:476px">Our <span>Services</span></h2>
<p class="section-sub" style="top:502px">Lorem Ipsum is simply dummy text of the printing and typesetting industry.</p>

<div class="service-card" style="left:59px">
  <div class="service-photo" role="img" aria-label="Technician sanding a car panel"></div>
  <div class="service-label">Panel Repairs</div>
</div>
<div class="service-card featured" style="left:262px">
  <div class="service-photo" role="img" aria-label="Mechanic working on a car body"></div>
  <div class="service-label">Panel Repairs</div>
  <div class="read-more">read more</div>
</div>
<div class="service-card" style="left:465px">
  <div class="service-photo" role="img" aria-label="Worker repairing a wheel arch"></div>
  <div class="service-label">Panel Repairs</div>
</div>

<h2 class="section-title" style="top:665px">Latest News <span>from Blog</span></h2>
<p class="section-sub" style="top:690px">Lorem Ipsum is simply dummy text of the printing and typesetting industry.</p>

<article class="post" style="left:59px">
  <div class="post-photo" role="img" aria-label="Car passing through a paint booth"></div>
  <p class="post-meta">MARCH 18, 2015 &nbsp;|&nbsp; 5 COMMENTS</p>
  <h3 class="post-title">THE STANDARD BLOG POST TITLE</h3>
  <p class="post-text">Our latest refinish brought a faded sedan back to showroom depth, with a full colour match across every panel and a clear coat that will hold its gloss.</p>
  <div class="post-author"><span class="avatar"></span>by admin &nbsp;|&nbsp; Share</div>
</article>
<article class="post" style="left:362px">
  <div class="post-photo" role="img" aria-label="Mechanic working under a car bonnet"></div>
  <p class="post-meta">MARCH 18, 2015 &nbsp;|&nbsp; 5 COMMENTS</p>
  <h3 class="post-title">THE STANDARD BLOG POST TITLE</h3>
  <p class="post-text">A quick guide to caring for fresh paint in the first weeks, from gentle washing to the right wax, so your finish keeps looking new for longer.</p>
  <div class="post-author"><span class="avatar"></span>by admin &nbsp;|&nbsp; Share</div>
</article>

<div class="divider" style="top:980px"><div class="line" style="left:25px"></div><div class="mark"><i></i><i class="blue"></i><i></i></div><div class="line" style="left:386px"></div></div>

<footer class="site-footer">
  <div class="footer-col" style="left:52px;width:120px">
    <h4>ABOUT US</h4>
    <div class="footer-brand">VELTRA</div>
    <p>Our bright team and skilled painters care for every panel and every car, giving each owner a finish they are proud of.</p>
    <p class="more">Read More</p>
  </div>
  <div class="footer-col" style="left:215px">
    <h4>SUPPORT LINKS</h4>
    <ul>
      <li>Home</li><li>Our Process</li><li>Private Customers</li><li>Fleet &amp; Corporate Insurance</li><li>Get a Quote</li><li>Contact</li>
    </ul>
  </div>
  <div class="footer-col" style="left:350px">
    <h4>NEWSLETTER SIGN UP</h4>
    <p>Sign up for news and offers</p>
    <div class="email-field">Email Address</div>
    <div class="subscribe">SUBSCRIBE</div>
  </div>
  <div class="footer-col" style="left:545px">
    <h4>SOCIAL MEDIA</h4>
    <div class="social"><span></span><span></span><span></span><span></span><span></span><span></span></div>
  </div>
  <p class="copyright">© 2015 Company Name . All rights reserved. Terms of Use</p>
</footer>

</body>
</html>
```